Tolvik Commercial Cleaning is lookong for a new business card design.

A fresh new design that's professional and stylish. We need a serious upgrade to our business cards. I have included pictures of our existing ones. Our clients include professional individuals and business owners. We woupdblike something professional and upbeat. Please have fun and see what you come uo with.

Target Market(s)

Property managers, business owners, facility managers and other similar professionals

Industry/Entity Type

Janitorial

Contact Information for Business Card

Name, cell, office number, email, web address

Font styles to use
Sans Serif

Colors

Designer to choose colors to be used in the design.

Requirements
Must have
• please use the green color in our logo
Nice to have
• Bar code
Should not have
• Address

```html
<!DOCTYPE html>
<html lang="en">
<head>
<meta charset="utf-8">
<title>Tolvik Commercial Cleaning – Business Card</title>
<link rel="stylesheet" href="https://fonts.googleapis.com/css2?family=Montserrat:wght@400;500;600;700&display=swap">
<style>
  :root {
    --brand-green: #43ae58;
    --name-green: #3ba94f;
    --card-white: #ffffff;
    --text-dark: #333333;
    --text-muted: #444444;
    --backdrop: #8a7458;
  }
  * { box-sizing: border-box; margin: 0; padding: 0; }
  html, body { width: 900px; height: 1200px; overflow: hidden; }
  body {
    background: var(--backdrop);
    font-family: "Montserrat", sans-serif;
    position: relative;
  }
  .card {
    position: absolute;
    left: 80px;
    width: 742px;
    height: 440px;
    border-radius: 30px;
    overflow: hidden;
  }
  .card--front { top: 132px; background: var(--card-white); }
  .card--back { top: 638px; background: var(--brand-green); }

  .brand-front {
    position: absolute;
    left: 46px;
    top: 96px;
    color: var(--brand-green);
    font-weight: 600;
    line-height: 1;
  }
  .brand-front .brand-main { display: block; font-size: 76px; letter-spacing: -1px; }
  .brand-front .brand-sub { display: block; font-size: 20px; margin-top: 12px; letter-spacing: 0.2px; }

  .person {
    position: absolute;
    right: 36px;
    top: 210px;
    text-align: right;
  }
  .person-name { font-size: 25px; font-weight: 700; color: var(--name-green); line-height: 1.1; }
  .person-title { font-size: 15px; font-weight: 400; color: var(--text-dark); margin-top: 4px; }

  .divider {
    position: absolute;
    left: 46px;
    top: 247px;
    width: 524px;
    height: 1.5px;
    background: var(--brand-green);
  }

  .contact-list {
    position: absolute;
    left: 43px;
    top: 263px;
    list-style: none;
  }
  .contact-list li {
    display: flex;
    align-items: center;
    height: 22px;
    font-size: 16px;
    color: var(--text-muted);
  }
  .contact-list svg { width: 14px; height: 14px; margin-right: 11px; fill: var(--brand-green); }

  .brand-back {
    position: absolute;
    left: 0; right: 0;
    top: 150px;
    text-align: center;
    color: var(--card-white);
    font-weight: 600;
    line-height: 1;
  }
  .brand-back .brand-main { display: block; font-size: 110px; letter-spacing: -2px; }
  .brand-back .brand-sub { display: block; font-size: 30px; margin-top: 20px; }
</style>
</head>
<body>
  <section class="card card--front">
    <div class="brand-front">
      <span class="brand-main">Tolvik</span>
      <span class="brand-sub">Commercial Cleaning</span>
    </div>

    <div class="person">
      <p class="person-name">Maren Oakley</p>
      <p class="person-title">CEO &amp; Founder</p>
    </div>

    <div class="divider"></div>

    <ul class="contact-list">
      <li>
        <svg viewBox="0 0 16 16" aria-hidden="true"><path d="M1 6c0-2 3-3 7-3s7 1 7 3v1h-3V5.5c-1-.4-2.5-.6-4-.6s-3 .2-4 .6V7H1zM3 8h10l1 6H2zm5 1.5a2 2 0 1 0 0 4 2 2 0 0 0 0-4z"/></svg>
        (37) 555-0182
      </li>
      <li>
        <svg viewBox="0 0 16 16" aria-hidden="true"><path d="M1 3h14v1.2L8 9 1 4.2zM1 5.6l7 4.8 7-4.8V13H1z"/></svg>
        maren@tolvikcleaning.com
      </li>
      <li>
        <svg viewBox="0 0 16 16" aria-hidden="true"><path d="M8 1a7 7 0 1 0 0 14A7 7 0 0 0 8 1zm-1 2.5c1 .5 1 1.5 0 2s-2 .5-2 1.5 1 1.5 2 2 .5 2-.5 2.5c-1.5-.7-3-2.5-3-4.5 0-1.5.8-2.8 2-3.5zm3 .3c1.5.8 2.5 2.4 2.5 4.2-1 .5-2-.5-2.5-1.5S9 4.5 10 3.8z"/></svg>
        www.tolvikcleaning.com
      </li>
    </ul>
  </section>

  <section class="card card--back">
    <div class="brand-back">
      <span class="brand-main">Tolvik</span>
      <span class="brand-sub">Commercial Cleaning</span>
    </div>
  </section>
</body>
</html>
```